Flat bootstrap design for existing site

I'm looking for a modern flat design based around an existing logo. This has to be a custom design (no external templates), and implemented into a bootstrap framework.

The logo is attached as 2 versions - choose whichever you want, that flows better with whatever design you choose.

Added screenshots of the existing site (currently using the default bootstrap layouts). Please make your designs around those pages in the screenshots (i.e. the homepage only has the postal code input and the header). The active page has 3 screenshots, because I wanted to illustrate the other states that would be visible (in the table rows).

This is a moving/junk removal website, just for some context.

Here's some example websites (flat designs) that I like, just to give you an idea of what I'm after.

https://www.plimvora.com/
https://dacklow.com/
https://trevanu.com/
https://quobrintal.com/en/

Coding

Coded - Design and coding required

Number of Pages Required

5+ page

Colors

Designer to choose colors to be used in the design.

Requirements
Must have
• It must be a modern/simple flat design, that is built around the existing logo (attached).
• It has to be implemented using bootstrap.

```html
<!DOCTYPE html>
<html lang="en">
<head>
<meta charset="utf-8">
<title>HAULVO – Booking details</title>
<link rel="stylesheet" href="https://fonts.googleapis.com/css2?family=Montserrat:wght@600;700;800&family=Mulish:wght@400;600;700&family=Roboto:wght@400;500&display=swap">
<style>
  :root{
    --sky:#38bdf2;
    --sky-deep:#2aa9e4;
    --violet:#6353c4;
    --violet-title:#5b4fb8;
    --navy-btn:#1a7fcc;
    --ink:#2b2b3a;
    --ink-soft:#3d3d4d;
    --line:#e2e4ea;
    --field-line:#d6d8df;
    --alert-bg:#d4ecf7;
    --alert-line:#a8d8ee;
    --badge:#dcdde2;
    --white:#ffffff;
  }
  *{box-sizing:border-box;margin:0;padding:0}
  html,body{width:1200px;height:774px;overflow:hidden}
  body{position:relative;background:var(--sky);font-family:"Mulish",sans-serif;color:var(--ink)}

  .site-header{position:absolute;left:0;top:0;width:1200px;height:80px}
  .brand{position:absolute;left:144px;top:18px;font-family:"Montserrat",sans-serif;font-weight:800;font-size:30px;color:var(--white);letter-spacing:1px}
  .nav{position:absolute;top:22px;left:0;width:1200px;height:34px}
  .nav-link{position:absolute;top:10px;font-family:"Montserrat",sans-serif;font-weight:700;font-size:11.5px;letter-spacing:.6px;color:var(--white);text-decoration:none}
  .nav-cta{position:absolute;left:738px;top:0;width:134px;height:34px;background:var(--navy-btn);color:var(--white);font-family:"Montserrat",sans-serif;font-weight:700;font-size:11.5px;letter-spacing:.6px;display:flex;align-items:center;justify-content:center;border-radius:2px}
  .account{position:absolute;left:889px;top:8px;display:flex;align-items:center;gap:6px;font-family:"Montserrat",sans-serif;font-weight:600;font-size:13px;color:var(--violet)}
  .account-dot{width:18px;height:18px;border-radius:50%;background:var(--violet)}

  .card{position:absolute;left:144px;width:912px;background:var(--white);border-radius:3px;box-shadow:0 2px 8px rgba(0,0,0,.06)}
  .card-head{height:46px;border-bottom:1px solid var(--line);display:flex;align-items:center;padding:0 15px;position:relative}
  .card-title{font-family:"Roboto",sans-serif;font-weight:400;font-size:19.5px;color:var(--violet-title)}
  .collapse-btn{position:absolute;right:15px;top:9px;width:28px;height:28px;border:1px solid #c9c6e6;border-radius:50%;display:flex;align-items:center;justify-content:center}

  .booking{top:102px;height:154px}
  .field-label{position:absolute;top:66px;font-size:13px;color:var(--ink)}
  .field{position:absolute;top:86px;height:36px;border:1px solid var(--field-line);border-radius:2px;display:flex;align-items:center;padding-left:11px;font-size:12.5px;color:var(--ink-soft)}
  .field.is-active{border-color:var(--violet)}
  .field-icon{position:absolute;right:0;top:0;height:34px;width:30px;border-left:1px solid var(--field-line);display:flex;align-items:center;justify-content:center}
  .btn-update{position:absolute;left:823px;top:86px;width:73px;height:36px;background:var(--violet);color:var(--white);font-family:"Montserrat",sans-serif;font-weight:700;font-size:11.5px;letter-spacing:.6px;display:flex;align-items:center;justify-content:center;border-radius:2px}

  .drivers{top:272px;height:336px}
  .drivers .card-head{height:48px}
  .notice{position:absolute;left:16px;top:64px;width:880px;height:36px;background:var(--alert-bg);border:1px solid var(--alert-line);border-radius:3px;font-size:12.5px;color:var(--ink-soft);display:flex;align-items:center;padding-left:19px}
  .driver-table{position:absolute;left:16px;top:122px;width:880px;border-collapse:collapse;font-size:12.5px}
  .driver-table th{text-align:left;font-weight:700;font-size:12.5px;height:32px;border-bottom:1.5px solid var(--line);color:var(--ink)}
  .driver-table td{height:41.6px;border-bottom:1px solid var(--line);color:var(--ink-soft)}
  .driver-table tr:last-child td{border-bottom:none}
  .col-name{width:230px}.col-dist{width:260px}.col-time{width:226px;text-align:center}
  .badge{display:inline-block;width:68px;height:17px;background:var(--badge);color:var(--white);font-size:11px;text-align:center;line-height:17px;border-radius:1px}

  .scene{position:absolute;left:1008px;top:548px;width:192px;height:160px;border-radius:120px 0 0 0;background:linear-gradient(160deg,#8fd8f7,#62c7f2)}

  .footer{position:absolute;left:0;top:708px;width:1200px;height:58px;background:var(--white)}
  .copyright{position:absolute;left:144px;top:22px;font-size:12px;color:var(--ink-soft)}
  .social{position:absolute;left:987px;top:23px;display:flex;gap:6px}
  .social span{width:18px;height:18px;background:#8a8fb3;border-radius:2px}
  .footer-band{position:absolute;left:0;top:766px;width:1200px;height:8px;background:var(--violet)}
</style>
</head>
<body>
  <header class="site-header">
    <div class="brand">HAULVO</div>
    <nav class="nav">
      <a class="nav-link" style="left:560px">BOOK</a>
      <a class="nav-link" style="left:621px">HOW IT WORKS</a>
      <div class="nav-cta">BECOME A DRIVER</div>
      <div class="account"><span class="account-dot"></span>corvin@mailtrove.com
        <svg width="9" height="6" viewBox="0 0 9 6"><path d="M1 1l3.5 3.5L8 1" fill="none" stroke="#6353c4" stroke-width="1.5"/></svg>
      </div>
    </nav>
  </header>

  <section class="card booking">
    <div class="card-head">
      <h2 class="card-title">Booking details</h2>
      <div class="collapse-btn"><svg width="10" height="7" viewBox="0 0 10 7"><path d="M1 6l4-4 4 4" fill="none" stroke="#6353c4" stroke-width="1.6"/></svg></div>
    </div>
    <label class="field-label" style="left:15px">Package selected:</label>
    <div class="field is-active" style="left:16px;width:202px">Package 1
      <svg style="position:absolute;right:6px;top:9px" width="9" height="17" viewBox="0 0 9 17"><path d="M1 5l3.5-3.5L8 5M1 12l3.5 3.5L8 12" fill="none" stroke="#6353c4" stroke-width="1.4"/></svg>
    </div>
    <label class="field-label" style="left:229px">Pick-up time selected:</label>
    <div class="field" style="left:230px;width:222px">July 18 at 4:13 am
      <span class="field-icon"><svg width="14" height="14" viewBox="0 0 14 14"><rect x="1" y="2.5" width="12" height="10.5" rx="1" fill="none" stroke="#6353c4" stroke-width="1.5"/><path d="M1 6h12M4 1v3M10 1v3" stroke="#6353c4" stroke-width="1.5"/></svg></span>
    </div>
    <label class="field-label" style="left:463px">Description:</label>
    <div class="field" style="left:464px;width:347px">1 Large Stove</div>
    <div class="btn-update">UPDATE</div>
  </section>

  <section class="card drivers">
    <div class="card-head"><h2 class="card-title">Drivers in your area</h2></div>
    <div class="notice">Please stay on this page and be patient, while we contact the drivers and find you one ASAP.</div>
    <table class="driver-table">
      <thead><tr><th class="col-name">Name</th><th class="col-dist">Distance (KM)</th><th style="width:160px">Agreed pick-up time</th><th></th></tr></thead>
      <tbody>
        <tr><td>Dorian Pell</td><td>4.04 KM away</td><td class="col-time">-</td><td><span class="badge">Pending</span></td></tr>
        <tr><td>Marcus Wend</td><td>5.07 KM away</td><td class="col-time">-</td><td><span class="badge">Pending</span></td></tr>
        <tr><td>Elias Frome</td><td>11.13 KM away</td><td class="col-time">-</td><td><span class="badge">Pending</span></td></tr>
        <tr><td>Victor Halden</td><td>11.91 KM away</td><td class="col-time">-</td><td><span class="badge">Pending</span></td></tr>
      </tbody>
    </table>
  </section>

  <div class="scene" role="img" aria-label="Illustration of a moving driver beside a house and a delivery van on a hill"></div>

  <footer class="footer">
    <p class="copyright">© 2017 HAULVO. All rights reserved.</p>
    <div class="social"><span></span><span></span><span></span></div>
  </footer>
  <div class="footer-band"></div>
</body>
</html>
```